Danielle Brooke Interiors business cards

We need a DOUBLE SIDED business card design that is simple, elegant and modern. We are a rapidly growing Interior Design Firm, and our brand colours are blush pink, navy, and antique gold, so we require some or all of these colours to be used. The final design should portray elegance, simplicity, and have a modern feel. We have upload inspiration photos that have the feel we're looking for.

Industry/Entity Type

Interior Design

Contact Information for Business Card

Contact information and LOGO

Colors
EB3D1F
EC4F4E
F09395
F8D3D4
FCEDEE

Requirements
Must have
• Navy, the right shade of blush pink, and antique gold

```html
<!DOCTYPE html>
<html lang="en">
<head>
<meta charset="utf-8">
<title>Danielle Brooke Interiors – Business Cards</title>
<link rel="stylesheet" href="https://fonts.googleapis.com/css2?family=Cinzel:wght@400&family=Jost:wght@400&family=Poppins:wght@300;400&display=swap">
<style>
  :root {
    --navy: #0f2258;
    --blush: #c98f84;
    --blush-light: #dba497;
    --blush-deep: #a8766d;
    --gold: #7d6a2c;
    --paper: #ffffff;
    --mist: #e9e9ea;
    --ink: #1d1d1f;
    --page: #ffffff;
  }
  * { box-sizing: border-box; margin: 0; padding: 0; }
  html, body { width: 687px; height: 1200px; overflow: hidden; background: var(--page); }
  .sheet {
    width: 687px; height: 1200px;
    display: flex; flex-direction: column; align-items: center; justify-content: center;
    gap: 60px;
  }
  .card {
    width: 600px; height: 343px; display: block;
    box-shadow: 0 2px 6px rgba(0,0,0,0.25);
  }
  .brand-name { font-family: "Jost", sans-serif; font-size: 36px; fill: var(--gold); letter-spacing: 0.5px; }
  .web { font-family: "Poppins", sans-serif; font-weight: 300; font-size: 24px; fill: var(--ink); }
  .person-name { font-family: "Cinzel", serif; font-size: 46px; fill: var(--ink); letter-spacing: 1px; }
  .person-title { font-family: "Cinzel", serif; font-size: 23px; fill: var(--gold); letter-spacing: 1px; }
  .contact { font-family: "Poppins", sans-serif; font-weight: 400; font-size: 26px; fill: var(--ink); }
  .follow-label { font-family: "Poppins", sans-serif; font-weight: 300; font-size: 19px; fill: var(--paper); }
  .social { font-family: "Poppins", sans-serif; font-weight: 300; font-size: 21px; fill: var(--ink); }
  .icon-dot { fill: var(--blush-light); }
  .icon-line { stroke: var(--paper); stroke-width: 2; fill: none; }
</style>
</head>
<body>
<main class="sheet">

  <!-- Front -->
  <svg class="card card-front" viewBox="0 0 944 540" aria-label="Business card front">
    <defs>
      <linearGradient id="paperFront" x1="0" y1="0" x2="1" y2="1">
        <stop offset="0" stop-color="#e4e4e5"/>
        <stop offset="0.5" stop-color="#f6f6f6"/>
        <stop offset="1" stop-color="#fbfbfb"/>
      </linearGradient>
      <linearGradient id="blushFront" x1="0" y1="0" x2="0.4" y2="1">
        <stop offset="0" stop-color="var(--blush-light)"/>
        <stop offset="0.6" stop-color="var(--blush)"/>
        <stop offset="1" stop-color="var(--blush-deep)"/>
      </linearGradient>
    </defs>
    <rect class="card-paper" width="944" height="540" fill="url(#paperFront)"/>
    <polygon class="band-navy" points="751,0 831,0 656,540 576,540" fill="var(--navy)"/>
    <polygon class="band-white" points="831,0 874,0 706,540 656,540" fill="var(--paper)"/>
    <polygon class="corner-navy" points="874,0 944,0 944,215" fill="var(--navy)"/>
    <polygon class="blush-facets" role="img" aria-label="Faceted blush pink texture"
             points="880,0 944,215 944,540 708,540" fill="url(#blushFront)"/>
    <line class="gold-edge" x1="880" y1="0" x2="708" y2="540" stroke="var(--gold)" stroke-width="2"/>
    <rect class="gold-base" x="0" y="530" width="708" height="10" fill="var(--gold)"/>
    <text class="brand-name" x="308" y="300" text-anchor="middle">DANIELLE BROOKE INTERIORS</text>
    <text class="web" x="308" y="468" text-anchor="middle">www.daniellebrookeinteriors.com</text>
  </svg>

  <!-- Back -->
  <svg class="card card-back" viewBox="0 0 944 540" aria-label="Business card back">
    <defs>
      <linearGradient id="paperBack" x1="0" y1="0" x2="1" y2="1">
        <stop offset="0" stop-color="#e6e6e7"/>
        <stop offset="0.45" stop-color="#f7f7f7"/>
        <stop offset="1" stop-color="#fcfcfc"/>
      </linearGradient>
      <linearGradient id="blushBack" x1="0" y1="0" x2="0.3" y2="1">
        <stop offset="0" stop-color="var(--blush-deep)"/>
        <stop offset="0.5" stop-color="var(--blush)"/>
        <stop offset="1" stop-color="var(--blush-light)"/>
      </linearGradient>
    </defs>
    <rect class="card-paper" width="944" height="540" fill="url(#paperBack)"/>
    <polygon class="band-navy" points="575,0 655,0 832,540 752,540" fill="var(--navy)"/>
    <polygon class="band-white" points="655,0 705,0 874,540 832,540" fill="var(--paper)"/>
    <polygon class="corner-navy" points="944,320 944,540 874,540" fill="var(--navy)"/>
    <polygon class="blush-facets" role="img" aria-label="Faceted blush pink texture"
             points="705,0 944,0 944,320 878,530" fill="url(#blushBack)"/>
    <line class="gold-edge" x1="705" y1="0" x2="878" y2="530" stroke="var(--gold)" stroke-width="2"/>

    <text class="person-name" x="84" y="128">DANIELLE BROOKE</text>
    <rect class="title-frame" x="84" y="138" width="282" height="28" fill="none" stroke="var(--gold)" stroke-width="1"/>
    <text class="person-title" x="90" y="161">PRINCIPAL DESIGNER</text>

    <g class="contact-row">
      <circle class="icon-dot" cx="100" cy="232" r="19"/>
      <path class="icon-line" d="M92 225 q0 14 14 14 l3 -4 -4 -3 -2 2 q-5 -2 -7 -7 l2 -2 -3 -4 z"/>
      <text class="contact" x="138" y="241">Office # 555-014-2273</text>
    </g>
    <g class="contact-row">
      <circle class="icon-dot" cx="100" cy="288" r="19"/>
      <rect class="icon-line" x="91" y="282" width="18" height="12"/>
      <path class="icon-line" d="M91 282 l9 7 9 -7"/>
      <text class="contact" x="138" y="297">danielle@dbinteriorsinc.com</text>
    </g>
    <g class="contact-row">
      <circle class="icon-dot" cx="100" cy="342" r="19"/>
      <circle class="icon-line" cx="100" cy="342" r="9"/>
      <path class="icon-line" d="M91 342 h18 M100 333 q-6 9 0 18 q6 -9 0 -18"/>
      <text class="contact" x="138" y="351">www.daniellebrookeinteriors.com</text>
    </g>

    <rect class="follow-tag" x="84" y="398" width="178" height="28" fill="var(--gold)"/>
    <text class="follow-label" x="96" y="419">FOLLOW ME ON</text>

    <circle class="social-dot" cx="90" cy="462" r="6" fill="var(--gold)"/>
    <text class="social" x="104" y="470">daniellebrookeinteriors</text>
    <rect class="social-dot" x="368" y="456" width="12" height="12" fill="var(--gold)"/>
    <text class="social" x="390" y="470">danielle.brooke.interiors</text>
  </svg>

</main>
</body>
</html>
```